NCBG website design

We need a page template website design for a cms website. Please see the brief attached for the details.
The client is the National Copperfleece Breeders Guild which is an organisation promoting the Copperfleece Sheep Breed within Australia.
Updates

Project Deadline Extended
Reason: So that my top few designs can make changes and re-submit.

Target Market(s)

See attached brief

```html
<!DOCTYPE html>
<html lang="en">
<head>
<meta charset="utf-8">
<title>Copperfleece – National Copperfleece Breeders Guild</title>
<link rel="stylesheet" href="https://fonts.googleapis.com/css2?family=Lato:wght@400;700&family=Oswald:wght@500&display=swap">
<style>
:root{
  --green:#17893a;
  --green-dark:#0f6e2c;
  --yellow:#f2c21b;
  --charcoal:#333436;
  --footer:#3a3b3d;
  --footer-base:#2c2d2f;
  --footer-chip:#55565a;
  --text:#3c3c3c;
  --band:#ececec;
}
*{box-sizing:border-box;margin:0;padding:0}
html,body{width:870px;height:1200px;overflow:hidden}
body{position:relative;background:#fff;font-family:"Lato",sans-serif;color:var(--text)}
.abs{position:absolute}

/* top bar */
.topbar{left:0;top:0;width:870px;height:19px;background:var(--green);border-bottom:1px solid var(--yellow)}
.helpline{left:96px;top:3px;font-size:11px;color:#fff}
.social-top{left:680px;top:5px;display:flex;gap:12px}
.social-top span{width:9px;height:9px;background:#fff;border-radius:2px;display:block}

/* header */
.header-bg{left:0;top:20px;width:870px;height:95px;background:linear-gradient(180deg,#eceae5,#f6f5f2 60%,#e9e7e1)}
.brand{left:96px;top:44px;display:flex;align-items:center;gap:8px}
.brand-mark{width:30px;height:30px;border-radius:50%;background:var(--green)}
.brand-name{font-size:22px;font-weight:700;color:var(--green)}
.account{left:672px;top:36px;width:102px;height:24px;background:var(--charcoal);border:1px solid var(--yellow);border-radius:3px;color:#fff;font-size:9px;display:flex;align-items:center;justify-content:space-between;padding:0 8px}
.account .or{width:14px;height:14px;border-radius:50%;background:var(--yellow);color:#333;font-size:5px;display:flex;align-items:center;justify-content:center;font-weight:700}
.search-box{left:604px;top:78px;width:136px;height:24px;border:1px solid #bbb;border-radius:3px;background:#fff;font-size:7.5px;font-style:italic;color:#888;padding:7px 8px}
.go{left:747px;top:78px;width:27px;height:24px;background:var(--green);border-radius:3px;color:#fff;font-size:9px;display:flex;align-items:center;justify-content:center}

/* nav */
.nav{left:0;top:115px;width:870px;height:34px;background:var(--green)}
.nav-item{top:125px;font-size:13px;color:#fff}
.nav-sep{top:124px;width:1px;height:17px;background:rgba(255,255,255,.3)}
.nav-home{left:90px;top:112px;width:70px;height:37px;background:var(--charcoal);color:#fff;font-size:13px;display:flex;align-items:center;justify-content:center;border-radius:3px 3px 0 0}
.nav-search{left:222px;top:121px;width:71px;height:30px;background:#fff;border-radius:3px 3px 0 0;color:var(--green);font-size:13px;padding:6px 0 0 17px}
.nav-search i{position:absolute;left:17px;top:22px;width:38px;height:1px;background:var(--green)}
.dropdown{left:222px;top:149px;width:136px;height:61px;background:#fff;border:1px solid var(--green);border-top:none;z-index:2}
.dropdown .member{position:absolute;left:8px;top:7px;width:120px;height:22px;background:linear-gradient(#fdfdfd,#ececec);border:1px solid #ddd;color:var(--green);font-size:11px;padding:4px 9px}
.dropdown .stud{position:absolute;left:17px;top:38px;font-size:11px;color:#777}

/* hero */
.hero{left:0;top:149px;width:870px;height:285px;background:linear-gradient(180deg,#b7c3c6 0%,#75896a 35%,#9a9a7e 60%,#6f9a3b 85%,#5d8d30 100%)}
.hero-title{left:0;top:238px;width:870px;text-align:center;font-family:"Oswald",sans-serif;font-weight:500;font-size:24px;color:#fff;letter-spacing:-.2px;text-shadow:0 1px 3px rgba(0,0,0,.6)}
.hero-sub{left:0;top:273px;width:870px;text-align:center;font-size:13px;color:#fff;text-shadow:0 1px 2px rgba(0,0,0,.6)}
.explore{left:383px;top:314px;width:103px;height:30px;background:var(--green);border-radius:3px;color:#fff;font-size:13px;display:flex;align-items:center;justify-content:center;box-shadow:0 2px 3px rgba(0,0,0,.3)}
.arrow{top:273px;width:32px;height:33px;background:rgba(255,255,255,.85);display:flex;align-items:center;justify-content:center}
.dots{left:397px;top:416px;display:flex;gap:7px}
.dots span{width:14px;height:14px;background:#fff;display:block}
.dots span.on{border:3px solid var(--green)}

/* feature band */
.band{left:0;top:434px;width:870px;height:111px;background:var(--band);border-top:1px solid #ccc}
.feature-box{top:468px;height:51px;background:var(--charcoal);border-radius:0 3px 3px 0;color:#fff;padding:8px 0 0 18px}
.feature-box.active{border:1px solid var(--yellow)}
.feature-box h3{font-weight:400;font-size:15px}
.feature-box p{font-size:9px;margin-top:4px}
.shield{top:456px}

/* welcome */
h2.section{font-weight:400;font-size:15px;color:#333}
h2.section b{font-weight:400;color:var(--green)}
.video{left:95px;top:606px;width:175px;height:97px;background:linear-gradient(180deg,#8aa0b0 0%,#6d6e4e 45%,#a58a66 75%,#4b4b3a 100%)}
.video-bar{left:95px;top:686px;width:175px;height:16px;background:#1e1e1e}
.video-bar i{position:absolute;left:34px;top:7px;width:90px;height:2px;background:#666}
.video-bar i::before{content:"";position:absolute;left:0;top:0;width:44px;height:2px;background:#ccc}
.play{left:170px;top:643px;width:22px;height:16px;background:#d8231e;border-radius:4px}
.body-copy{font-size:8.6px;line-height:12.4px;color:#444}
.btn{background:var(--green);color:#fff;font-size:9.5px;display:flex;align-items:center;justify-content:center;border-radius:2px;border-bottom:2px solid var(--green-dark)}
.divider-v{left:558px;top:572px;width:1px;height:192px;background:#e2e2e2}
.field{left:582px;width:192px;border:1px solid #ccc;border-radius:2px;background:#fff;font-size:8.5px;color:#777;padding:4px 7px;box-shadow:inset 0 1px 2px rgba(0,0,0,.06)}
.rule{left:96px;top:796px;width:678px;height:1px;background:#e4e4e4}

/* gallery */
.card{top:848px;width:116px;height:115px;background:#f2f2f2;border:1px solid #ddd}
.card.active{border-color:var(--yellow)}
.card .photo{position:absolute;left:6px;top:5px;width:104px;height:87px}
.card .stats{position:absolute;left:7px;top:98px;font-size:9px;color:#555;display:flex;align-items:center;gap:4px}
.card .stats svg{display:block}

/* footer */
.footer{left:0;top:1002px;width:870px;height:168px;background:var(--footer)}
.footer-base{left:0;top:1170px;width:870px;height:30px;background:var(--footer-base);color:#ddd;font-size:9px;text-align:center;padding-top:11px}
.f-head{top:1019px;font-size:15px;color:#fff;font-weight:400}
.f-line{top:1042px;height:1px;background:#5c5d60}
.f-text{font-size:9px;color:#e8e8e8;line-height:15px}
.f-input{left:96px;width:156px;height:18px;background:#59595b;font-size:8px;color:#ddd;padding:4px 5px}
.follow{left:682px;display:flex;align-items:center;gap:15px;font-size:9px;color:#eee}
.follow span{width:21px;height:21px;background:var(--footer-chip);border-radius:2px;display:block}
.sponsor{left:513px;top:1110px;width:102px;text-align:center;color:#777;font-size:12px;font-weight:700;letter-spacing:1px}
.sponsor small{display:block;font-size:6px;letter-spacing:1px;font-weight:700;margin-top:2px}
.sp-arrow{top:1087px;width:13px;height:13px;border-radius:50%;background:#ddd;display:flex;align-items:center;justify-content:center}
</style>
</head>
<body>

<!-- top bar -->
<div class="abs topbar"></div>
<div class="abs helpline">Prime Lamb Helpline</div>
<div class="abs social-top" aria-label="Social links"><span></span><span></span><span></span><span></span><span></span></div>

<!-- header -->
<div class="abs header-bg" role="img" aria-label="Faded photo of a sheep flock behind the header"></div>
<div class="abs brand"><span class="brand-mark"></span><span class="brand-name">Copperfleece</span></div>
<div class="abs account"><span>Login</span><span class="or">OR</span><span>Signup</span></div>
<div class="abs search-box">Search here......</div>
<div class="abs go">GO</div>

<!-- navigation -->
<div class="abs nav"></div>
<div class="abs nav-home">Home</div>
<div class="abs nav-item" style="left:174px">About</div>
<div class="abs nav-search">Search<i></i></div>
<div class="abs nav-item" style="left:312px">Member Services</div>
<div class="abs nav-sep" style="left:425px"></div>
<div class="abs nav-item" style="left:440px">Stud Pages</div>
<div class="abs nav-sep" style="left:516px"></div>
<div class="abs nav-item" style="left:533px">News</div>
<div class="abs nav-sep" style="left:580px"></div>
<div class="abs nav-item" style="left:596px">Sales</div>
<div class="abs nav-sep" style="left:642px"></div>
<div class="abs nav-item" style="left:658px">Link</div>
<div class="abs nav-sep" style="left:698px"></div>
<div class="abs nav-item" style="left:714px">Contact Us</div>
<div class="abs dropdown"><div class="member">Member</div><div class="stud">Stud</div></div>

<!-- hero -->
<div class="abs hero" role="img" aria-label="Flock of Copperfleece sheep grazing on a green paddock below wooded hills"></div>
<div class="abs hero-title">THE COPPERFLEECE IS AN AUSTRALIAN SHEEP BREED DEVELOPMENT</div>
<div class="abs hero-sub">we helps to market, promote and educate people about the advantages of the breed.</div>
<div class="abs explore">EXPLORE</div>
<div class="abs arrow" style="left:0;border-radius:0 4px 4px 0"><svg width="10" height="14" viewBox="0 0 10 14"><path d="M8 1 2 7l6 6" fill="none" stroke="#222" stroke-width="2"/></svg></div>
<div class="abs arrow" style="left:838px;border-radius:4px 0 0 4px"><svg width="10" height="14" viewBox="0 0 10 14"><path d="M2 1l6 6-6 6" fill="none" stroke="#222" stroke-width="2"/></svg></div>
<div class="abs dots"><span></span><span class="on"></span><span></span><span></span></div>

<!-- feature band -->
<div class="abs band"></div>

<div class="abs feature-box active" style="left:158px;width:139px"><h3>Recent Events</h3><p>Nam vitae sem vitae lectus</p></div>
<div class="abs feature-box" style="left:398px;width:138px"><h3>Our Members</h3><p>Nam vitae sem ve lectus</p></div>
<div class="abs feature-box" style="left:640px;width:134px"><h3>Latest News</h3><p>Nam vitae sem ve lectus</p></div>

<svg class="abs shield" style="left:96px" width="66" height="74" viewBox="0 0 66 74">
  <path d="M4 4q14 4 29-2 15 6 29 2v34q0 22-29 34Q4 60 4 38z" fill="var(--green)" stroke="var(--yellow)" stroke-width="3"/>
  <rect x="20" y="24" width="26" height="24" rx="2" fill="none" stroke="#fff" stroke-width="2.5"/>
  <rect x="20" y="24" width="26" height="6" fill="#fff"/>
  <g fill="#fff"><rect x="24" y="33" width="4" height="4"/><rect x="31" y="33" width="4" height="4"/><rect x="38" y="33" width="4" height="4"/><rect x="24" y="40" width="4" height="4"/><rect x="31" y="40" width="4" height="4"/><rect x="38" y="40" width="4" height="4"/></g>
</svg>
<svg class="abs shield" style="left:334px" width="66" height="74" viewBox="0 0 66 74">
  <path d="M4 4q14 4 29-2 15 6 29 2v34q0 22-29 34Q4 60 4 38z" fill="var(--green)" stroke="var(--yellow)" stroke-width="3"/>
  <circle cx="33" cy="28" r="7" fill="#fff"/>
  <path d="M19 50q1-13 14-13t14 13z" fill="#fff"/>
</svg>
<svg class="abs shield" style="left:573px" width="66" height="74" viewBox="0 0 66 74">
  <path d="M4 4q14 4 29-2 15 6 29 2v34q0 22-29 34Q4 60 4 38z" fill="var(--green)" stroke="var(--yellow)" stroke-width="3"/>
  <circle cx="33" cy="25" r="5" fill="#fff"/>
  <path d="M19 34l14 4 14-4v14l-14 4-14-4z" fill="#fff"/>
  <path d="M33 38v14" stroke="var(--green)" stroke-width="1.5"/>
</svg>

<!-- welcome -->
<h2 class="abs section" style="left:96px;top:574px">Welcome to <b>Copperfleece</b></h2>
<div class="abs video" role="img" aria-label="Video still of a line of sheep in a paddock"></div>
<div class="abs play"></div>
<svg class="abs" style="left:178px;top:647px" width="8" height="8" viewBox="0 0 8 8"><path d="M1 0l7 4-7 4z" fill="#fff"/></svg>
<div class="abs video-bar"><svg style="position:absolute;left:6px;top:4px" width="20" height="8" viewBox="0 0 20 8"><path d="M0 0l6 4-6 4z" fill="#fff"/><path d="M12 2h2l3-2v8l-3-2h-2z" fill="#fff"/></svg><i></i></div>

<p class="abs body-copy" style="left:277px;top:604px;width:260px">Curabitur interdum felis et massa mattis laoreet. Quisque pretium leo ante, vitae dictum elit aliquet non. Cras sed posuerefelis.Nam mi ipsum, aliquet sed lorem quis, sagittis pharetra ligula.Crasarcu velit, laoreet eget pretium interdum, auctor eget enim. Quisquesit ametdiamatmassaimperdietvariusacetneque.Vivamuselementum sodales erat, id condimentum augue facilisis in. Aenean sit amet pharetranulla.Namidantequisnequecommodovestibulumelementu m et ante. Classaptenttacitisocio.</p>
<p class="abs body-copy" style="left:95px;top:705px;width:442px">Aenean id est vitae sem porta tempus vitae vehicula enim. In accumsan ante ac nunc dapibus, eu euismod ligula luctus. Sed consectetur urna et lorem laoreet viverra. Integer ipsum tortor, interdum eget velit id, rhoncus</p>
<div class="abs btn" style="left:95px;top:741px;width:56px;height:21px">Read More</div>

<div class="abs divider-v"></div>

<!-- quick contact -->
<svg class="abs" style="left:580px;top:570px" width="28" height="26" viewBox="0 0 28 26" fill="none" stroke="#555" stroke-width="1.6">
  <path d="M9 24v-9l-5-5 2-2 5 4V3h2v9-11h2v11-10h2v10-8h2v14q0 6-6 10z"/>
  <path d="M2 3l3 3M1 9h3"/>
</svg>
<h2 class="abs section" style="left:619px;top:574px">Quick <b>Contact</b></h2>
<div class="abs field" style="top:606px;height:20px">Name</div>
<div class="abs field" style="top:630px;height:20px">Email</div>
<div class="abs field" style="top:654px;height:20px">Phone</div>
<div class="abs field" style="top:678px;height:45px">Comment</div>
<div class="abs btn" style="left:582px;top:741px;width:42px;height:21px">Send</div>

<div class="abs rule"></div>

<!-- gallery -->
<h2 class="abs section" style="left:96px;top:819px">Our <b>Gallery</b></h2>

<div class="abs card active" style="left:95px">
  <div class="photo" role="img" aria-label="Copperfleece ram standing on grass" style="background:linear-gradient(180deg,#4f7a3a,#c9c7bd 55%,#6d9a3e)"></div>
  <div class="stats"><svg width="15" height="9" viewBox="0 0 15 9"><path d="M0 4.5Q7.5-3 15 4.5 7.5 12 0 4.5z" fill="#555"/><circle cx="7.5" cy="4.5" r="2" fill="#f2f2f2"/></svg>123&nbsp;&nbsp;<svg width="9" height="8" viewBox="0 0 9 8"><path d="M4.5 8L0 3.5A2.2 2.2 0 014.5 1a2.2 2.2 0 014.5 2.5z" fill="#555"/></svg>4</div>
</div>
<div class="abs card" style="left:236px">
  <div class="photo" role="img" aria-label="Woolly sheep huddled together" style="background:linear-gradient(180deg,#6b6a4a,#a9865c 50%,#7a5d3b)"></div>
  <div class="stats"><svg width="15" height="9" viewBox="0 0 15 9"><path d="M0 4.5Q7.5-3 15 4.5 7.5 12 0 4.5z" fill="#555"/><circle cx="7.5" cy="4.5" r="2" fill="#f2f2f2"/></svg>423&nbsp;&nbsp;<svg width="9" height="8" viewBox="0 0 9 8"><path d="M4.5 8L0 3.5A2.2 2.2 0 014.5 1a2.2 2.2 0 014.5 2.5z" fill="#555"/></svg>10</div>
</div>
<div class="abs card" style="left:377px">
  <div class="photo" role="img" aria-label="Group of sheep in a yard" style="background:linear-gradient(180deg,#9aa59a,#b59a78 50%,#8a7657)"></div>
  <div class="stats"><svg width="15" height="9" viewBox="0 0 15 9"><path d="M0 4.5Q7.5-3 15 4.5 7.5 12 0 4.5z" fill="#555"/><circle cx="7.5" cy="4.5" r="2" fill="#f2f2f2"/></svg>100&nbsp;&nbsp;<svg width="9" height="8" viewBox="0 0 9 8"><path d="M4.5 8L0 3.5A2.2 2.2 0 014.5 1a2.2 2.2 0 014.5 2.5z" fill="#555"/></svg>24</div>
</div>
<div class="abs card" style="left:518px">
  <div class="photo" role="img" aria-label="Sheep resting under a tree" style="background:linear-gradient(180deg,#6e6a52,#cfcab8 50%,#7f8a55)"></div>
  <div class="stats"><svg width="15" height="9" viewBox="0 0 15 9"><path d="M0 4.5Q7.5-3 15 4.5 7.5 12 0 4.5z" fill="#555"/><circle cx="7.5" cy="4.5" r="2" fill="#f2f2f2"/></svg>104&nbsp;&nbsp;<svg width="9" height="8" viewBox="0 0 9 8"><path d="M4.5 8L0 3.5A2.2 2.2 0 014.5 1a2.2 2.2 0 014.5 2.5z" fill="#555"/></svg>11</div>
</div>
<div class="abs card" style="left:659px">
  <div class="photo" role="img" aria-label="Close group of white lambs" style="background:linear-gradient(180deg,#7fa05a,#e3e0d8 55%,#cfcbc0)"></div>
  <div class="stats"><svg width="15" height="9" viewBox="0 0 15 9"><path d="M0 4.5Q7.5-3 15 4.5 7.5 12 0 4.5z" fill="#555"/><circle cx="7.5" cy="4.5" r="2" fill="#f2f2f2"/></svg>189&nbsp;&nbsp;<svg width="9" height="8" viewBox="0 0 9 8"><path d="M4.5 8L0 3.5A2.2 2.2 0 014.5 1a2.2 2.2 0 014.5 2.5z" fill="#555"/></svg>2</div>
</div>

<!-- footer -->
<div class="abs footer"></div>

<h3 class="abs f-head" style="left:96px">Newsletter</h3>
<div class="abs f-line" style="left:96px;width:156px"></div>
<p class="abs f-text" style="left:97px;top:1048px;width:160px;line-height:13px">Signup with us and get update in your inbox.</p>
<div class="abs f-input" style="top:1082px">Your Name</div>
<div class="abs f-input" style="top:1107px">Email address</div>
<div class="abs btn" style="left:96px;top:1134px;width:64px;height:19px;font-weight:700;font-size:9px">SUBSCRIBE</div>

<h3 class="abs f-head" style="left:305px">Contact Us</h3>
<div class="abs f-line" style="left:305px;width:163px"></div>
<svg class="abs" style="left:304px;top:1053px" width="10" height="14" viewBox="0 0 10 14"><path d="M5 14S0 7 0 5a5 5 0 0110 0c0 2-5 9-5 9z" fill="#fff"/><circle cx="5" cy="5" r="2" fill="var(--footer)"/></svg>
<p class="abs f-text" style="left:325px;top:1049px">Lorem ipsum dolor sit amet<br>consectetur adipiscing elit,<br>Steet No.2-4567891</p>
<svg class="abs" style="left:305px;top:1107px" width="8" height="12" viewBox="0 0 8 12"><rect x="0.5" y="0.5" width="7" height="11" rx="1" fill="none" stroke="#fff"/><rect x="2" y="2" width="4" height="6" fill="#fff"/></svg>
<p class="abs f-text" style="left:325px;top:1106px;font-size:10px">(08) 8000 4172</p>
<svg class="abs" style="left:301px;top:1132px" width="14" height="10" viewBox="0 0 14 10"><rect x="0.5" y="0.5" width="13" height="9" fill="none" stroke="#fff"/><path d="M.5.5 7 6l6.5-5.5" fill="none" stroke="#fff"/></svg>
<p class="abs f-text" style="left:325px;top:1130px">info@copperfleece.com</p>

<h3 class="abs f-head" style="left:497px">Our Sponsors</h3>
<div class="abs f-line" style="left:497px;width:136px"></div>
<div class="abs sp-arrow" style="left:496px"><svg width="5" height="7" viewBox="0 0 5 7"><path d="M5 0v7L0 3.5z" fill="#3a3b3d"/></svg></div>
<div class="abs sp-arrow" style="left:621px"><svg width="5" height="7" viewBox="0 0 5 7"><path d="M0 0v7l5-3.5z" fill="#3a3b3d"/></svg></div>
<div class="abs" style="left:551px;top:1058px;width:26px;height:26px;border-radius:50%;background:#5a5b5e"></div>
<div class="abs sponsor">MERIDIAN<small>MEDIA GROUP</small></div>

<h3 class="abs f-head" style="left:682px">Follow Us On</h3>
<div class="abs follow" style="top:1050px"><span></span>Flockbook</div>
<div class="abs follow" style="top:1078px"><span></span>Chirpline</div>
<div class="abs follow" style="top:1107px"><span></span>Reelhouse</div>
<div class="abs follow" style="top:1135px"><span></span>Linkfold</div>

<div class="abs footer-base">Copyright © 2014 Copperfleece. All Rights Reserved.</div>

</body>
</html>
```